Build a landing page to promote a service (dialler consultation and support).

We are a call centre consultation firm and we need a landing page to promote a service. The service is Tormalux dialler consultation and support.
If you do not know what Tormalux is, please do some quick "Zorvex" research for more information.
The landing page will be promoted with a paid advertisement, so we want something that is simple, and explains exactly what service we offer.
There are two objectives for the landing page:
1) A "call to action" which directs the user to a contact page, including a form plus all of our contact details.
2) A form for them viewers to enter their details to get a "FREE" quote for their project. This form should be placed on the main page.
Notes:
The call to action will require the viewer to enter their name, email, phone number as well as a description of their request. There will also need to be a drop down menu for the type of quote. This menu should have the following options:
1) Tormalux support
2) Tormalux hosting
3) Tormalux customisation
4) Other
We need 2 pages in total:
1) Main landing page
This is the home page. It will need to clearly indicate our services and our key selling features.
Services:
* Tormalux support
* Tormalux hosting
* Tormalux customisation
Key Selling Features:
* Australian based
* PCI complaint
* 10+ years of dialler and call centre experience
* we run a sister company which is a highly reputable 40 seat call centre, so we know first hand about call centre technology.
The main landing page will have an "about us" section with a few paragraphs about how we got started.
-------------------------------------------------------------------------
2) Contact page
All of our contact details will live on this page, as well as a contact form.
Other notes:
We will be self hosting the landing page.
We already have a domain name.
The design must be clean and incorporate our logo, as well as it's colours. (Logo attached)
We want a fully function HTML landing page, not just a "PSD" design.
The page must be mobile optimised.
Anyone using Tormalux software.

```html
<!DOCTYPE html>
<html lang="en">
<head>
<meta charset="utf-8">
<title>Kestrel Voice – Tormalux Consultation and Support</title>
<link rel="stylesheet" href="https://fonts.googleapis.com/css2?family=Montserrat:wght@400;500;600;700&family=Open+Sans:wght@400;600&display=swap">
<style>
:root{
  --blue:#1f7cc5;
  --teal:#2db394;
  --ink:#2b2b2b;
  --body:#444;
  --grey-band:#f0f0f0;
  --footer:#3a3a3a;
  --white:#fff;
}
*{box-sizing:border-box;margin:0;padding:0}
html,body{width:738px;height:1200px;overflow:hidden;background:var(--white)}
body{position:relative;font-family:"Open Sans",Arial,sans-serif;color:var(--body)}
.abs{position:absolute}

/* header */
.site-header{position:absolute;left:0;top:0;width:738px;height:60px;background:var(--white)}
.brand{left:82px;top:10px;display:flex;flex-direction:column;align-items:center;gap:3px}
.brand-mark{width:26px;height:26px;border-radius:50%;background:var(--blue)}
.brand-name{font-family:"Montserrat",sans-serif;font-weight:600;font-size:11px;color:var(--blue)}
.main-nav{left:333px;top:21px;display:flex;gap:0;font-family:"Open Sans",sans-serif;font-size:10.5px;color:#555}
.main-nav a{color:inherit;text-decoration:none;margin-right:25px}
.contact-btn{left:571px;top:18px;width:86px;height:22px;border-radius:11px;background:var(--blue);color:var(--white);
  font-family:"Montserrat",sans-serif;font-weight:700;font-size:7.5px;display:flex;align-items:center;justify-content:center;gap:5px;text-decoration:none}

/* hero */
.hero{left:0;top:60px;width:738px;height:318px;background:linear-gradient(100deg,#8a8275 0%,#c9bba6 30%,#e0d6c8 45%,#7d8c99 75%,#d9d4cc 100%)}
.hero-headline{left:82px;top:121px;font-family:"Montserrat",sans-serif;font-weight:700;font-size:17.5px;line-height:24px;color:var(--ink)}
.slide-arrow{top:149px;width:20px;height:20px;border-radius:50%;background:var(--teal);border:2px solid var(--white)}
.slide-arrow svg{display:block;margin:3px auto 0}
.quote-box{left:399px;top:22px;width:257px;height:239px;background:rgba(43,176,143,.93)}
.quote-title{left:0;top:14px;width:100%;text-align:center;font-family:"Open Sans",sans-serif;font-weight:600;font-size:19px;letter-spacing:.5px;color:var(--white)}
.field{background:var(--white);height:22px;font-size:7px;color:#555;padding:7px 9px}
.field.select{display:flex;justify-content:space-between}
.field.area{height:66px}
.submit-btn{left:98px;top:198px;width:61px;height:21px;background:#2a2a2a;color:var(--white);font-family:"Montserrat",sans-serif;font-size:9.5px;display:flex;align-items:center;justify-content:center}

/* services */
.section-title{font-family:"Montserrat",sans-serif;font-weight:600;font-size:20px;color:var(--blue);text-align:center}
.service-card{top:458px;width:181px;height:154px;background:linear-gradient(180deg,var(--teal) 0%,var(--blue) 100%);color:var(--white);text-align:center}
.service-card svg{display:block;margin:14px auto 0}
.service-name{font-family:"Montserrat",sans-serif;font-weight:500;font-size:9.5px;margin-top:8px}
.service-text{font-size:6.4px;line-height:10.5px;margin:4px 18px 0}
.outline-btn{display:inline-block;margin-top:7px;width:58px;height:20px;line-height:18px;border:1px solid var(--white);font-family:"Montserrat",sans-serif;font-size:6.4px}

/* features */
.features{left:0;top:657px;width:369px;height:222px;background:var(--grey-band)}
.features-title{left:81px;top:42px;font-family:"Montserrat",sans-serif;font-weight:600;font-size:20px;color:var(--blue)}
.feature-list{left:81px;top:75px;list-style:none;font-family:"Montserrat",sans-serif;font-size:8px;color:var(--ink)}
.feature-list li{position:relative;padding-left:10px;line-height:13px;margin-bottom:12.6px}
.feature-list li::before{content:"";position:absolute;left:0;top:4px;width:3.5px;height:3.5px;border-right:1px solid var(--ink);border-top:1px solid var(--ink);transform:rotate(45deg)}
.features-photo{left:369px;top:657px;width:369px;height:222px;background:linear-gradient(120deg,#8a5a44 0%,#d8d2c6 40%,#b99670 65%,#e9e6e1 100%)}

/* about */
.about-text{left:82px;width:574px;font-size:6.9px;line-height:14px;text-align:justify;text-align-last:center;color:var(--body)}
.about-btn{left:340px;top:1057px;width:58px;height:20px;border:1px solid var(--blue);color:var(--blue);font-family:"Montserrat",sans-serif;font-size:6.4px;display:flex;align-items:center;justify-content:center}

/* footer */
.site-footer{left:0;top:1126px;width:738px;height:74px;background:var(--footer);color:#d5d5d5;font-size:7px}
.footer-nav{left:82px;top:24px}
.footer-nav span{margin:0 5px}
.copyright{left:82px;top:42px}
.social{top:29px;width:9px;height:9px;border-radius:50%;background:#cfcfcf}
</style>
</head>
<body>

<header class="site-header">
  <div class="abs brand"><span class="brand-mark"></span><span class="brand-name">Kestrel Voice</span></div>
  <nav class="abs main-nav"><a href="#">Home</a><a href="#">About Us</a><a href="#">Services</a><a href="#">Features</a></nav>
  <a class="abs contact-btn" href="#"><svg width="8" height="6" viewBox="0 0 8 6"><rect width="8" height="6" rx="1" fill="#fff"/><path d="M0.5 .8 4 3.4 7.5 .8" stroke="#1f7cc5" fill="none" stroke-width=".8"/></svg>CONTACT US</a>
</header>

<section class="abs hero" role="img" aria-label="Smiling call centre agent on a desk phone in a bright office">
</section>
<h1 class="abs hero-headline">VESTIBULUM<br>CONDIMENTUM<br>RISUS POSUERE</h1>
<div class="abs slide-arrow" style="left:28px"><svg width="10" height="10" viewBox="0 0 10 10"><path d="M6.5 1.5 3 5l3.5 3.5" stroke="#fff" stroke-width="1.8" fill="none"/></svg></div>
<div class="abs slide-arrow" style="left:690px"><svg width="10" height="10" viewBox="0 0 10 10"><path d="M3.5 1.5 7 5 3.5 8.5" stroke="#fff" stroke-width="1.8" fill="none"/></svg></div>

<form class="abs quote-box" style="top:82px">
  <div class="abs quote-title">FREE QUOTE</div>
  <div class="abs field" style="left:7px;top:51px;width:115px">Name</div>
  <div class="abs field" style="left:136px;top:51px;width:115px">Email</div>
  <div class="abs field" style="left:7px;top:85px;width:115px">Phone Number</div>
  <div class="abs field select" style="left:136px;top:85px;width:115px"><span>For Tormalux support</span><svg width="6" height="4" viewBox="0 0 6 4"><path d="M0 0h6L3 4z" fill="#444"/></svg></div>
  <div class="abs field area" style="left:7px;top:120px;width:244px">Description</div>
  <div class="abs submit-btn">SUBMIT</div>
</form>

<h2 class="abs section-title" style="left:0;top:421px;width:738px">SERVICES</h2>

<article class="abs service-card" style="left:81px">
  <svg width="40" height="40" viewBox="0 0 40 40" fill="none" stroke="#fff" stroke-width="1.3"><circle cx="20" cy="13" r="7"/><path d="M12 13a8 8 0 0 1 16 0M9 38c0-8 5-13 11-13s11 5 11 13M6 38h28M15 32h10v6H15z"/></svg>
  <div class="service-name">TORMALUX SUPPORT</div>
  <p class="service-text">Maecenas vel tortor accumsan quam varius imperdiet vel eget elit. Aenean facilisis tincidunt lectus, id dictum nisi luctus eget.</p>
  <span class="outline-btn">READ MORE</span>
</article>
<article class="abs service-card" style="left:279px">
  <svg width="40" height="40" viewBox="0 0 40 40" fill="none" stroke="#fff" stroke-width="1.3"><rect x="8" y="3" width="24" height="9" rx="1"/><rect x="8" y="14" width="24" height="9" rx="1"/><circle cx="12" cy="7.5" r="1.5"/><circle cx="12" cy="18.5" r="1.5"/><path d="M20 23v9M3 34h14M23 34h14"/><circle cx="20" cy="34" r="2.5"/></svg>
  <div class="service-name">TORMALUX HOSTING</div>
  <p class="service-text">Maecenas vel tortor accumsan quam varius imperdiet vel eget elit. Aenean facilisis tincidunt lectus, id dictum nisi luctus eget.</p>
  <span class="outline-btn">READ MORE</span>
</article>
<article class="abs service-card" style="left:476px">
  <svg width="40" height="40" viewBox="0 0 40 40" fill="none" stroke="#fff" stroke-width="1.3"><circle cx="9" cy="13" r="4"/><circle cx="29" cy="8" r="5"/><circle cx="28" cy="30" r="4"/><path d="M6 35l17-17M4 33l4 4"/></svg>
  <div class="service-name">TORMALUX CUSTOMISATION</div>
  <p class="service-text">Maecenas vel tortor accumsan quam varius imperdiet vel eget elit. Aenean facilisis tincidunt lectus, id dictum nisi luctus eget.</p>
  <span class="outline-btn">READ MORE</span>
</article>

<section class="abs features">
  <h2 class="abs features-title">FEATURES</h2>
  <ul class="abs feature-list">
    <li>Australian based</li>
    <li>PCI complaint</li>
    <li>10+ years of dialler and call centre experience</li>
    <li>we run a sister company which is a highly reputable 40 seat<br>call centre, so we know first hand about call centre technology.</li>
  </ul>
</section>
<div class="abs features-photo" role="img" aria-label="Team working on laptops at wooden tables in a brick-walled office"></div>

<h2 class="abs section-title" style="left:0;top:922px;width:738px">ABOUT US</h2>
<p class="abs about-text" style="top:950px">Aliquam erat volutpat. Quisque aliquet ex nec est vestibulum pulvinar. Pellentesque convallis molestie enim sit amet efficitur. Etiam id imperdiet lectus. Vivamus lacus justo, ultrices nec erat in, euismod iaculis mauris. Vivamus eleifend vitae nulla vel malesuada. In ac malesuada lacus, et consectetur ante. Fusce vitae lectus sit amet mi pulvinar maximus. Aenean placerat, nibh vel accumsan aliquet, magna nibh accumsan nibh, ac tempus nunc ipsum ac tellus. Cras augue magna, placerat eget nulla non, congue suscipit neque.</p>
<p class="abs about-text" style="top:1006px">Proin a dolor mauris. Vestibulum ante ipsum primis in faucibus orci luctus et ultrices posuere cubilia Curae; Vestibulum eget nisl metus. Phasellus nisl est, condimentum vitae faucibus in, sollicitudin vel metus. Nunc sit amet consequat risus. Curabitur ac elit leo. In eleifend dui tellus, in scelerisque elit porttitor et. Integer eu massa lacinia, lacinia nulla non, volutpat purus. Sed libero felis, vestibulum et dolor eget, lacinia aliquet neque.</p>
<a class="abs about-btn">READ MORE</a>

<footer class="abs site-footer">
  <div class="abs footer-nav">Home<span>|</span>About Us<span>|</span>Services<span>|</span>Features<span>|</span>Contact Us</div>
  <div class="abs copyright">Copyright © 2018 Kestrel Voice. &nbsp;All rights reserved</div>
  <span class="abs social" style="left:624px"></span>
  <span class="abs social" style="left:646px"></span>
</footer>

</body>
</html>
```